A clean crisp business card for a Landscape Construction company. Designed to be easy to read contact/ info and also be appealing/interesting, unlike a traditional business card.

Industry/Entity Type

Landscape Construction

Contact Information for Business Card

Company name : Brambleford Landscape Construction, phone number: (877) 62Vista, website:Bramblefordyards.example, Email, sales@bramblefordyards.example

Requirements
Nice to have
• Luxurious finishes/ details…. Icons or emblems next to contact info
Should not have
• Clipart or general pictures

```html
<!DOCTYPE html>
<html lang="en">
<head>
<meta charset="utf-8">
<title>Brambleford Landscape Construction – Business Card</title>
<link rel="stylesheet" href="https://fonts.googleapis.com/css2?family=Cinzel:wght@400;600&family=Lato:wght@400&display=swap">
<style>
  :root {
    --backdrop: #2a2a2b;
    --card: #1c1d1f;
    --card-deep: #141516;
    --blue: #1a6fc9;
    --green: #9ccc2e;
    --ink: #f2f2f2;
    --rule: #8a8a8a;
    --pattern-light: #3a3b3e;
    --pattern-dark: #18191b;
  }
  * { box-sizing: border-box; margin: 0; padding: 0; }
  html, body { width: 1200px; height: 1108px; overflow: hidden; }
  body {
    background: var(--backdrop);
    display: flex;
    align-items: center;
    justify-content: center;
    gap: 80px;
    font-family: "Lato", sans-serif;
  }
  .card {
    width: 400px;
    height: 660px;
    border-radius: 26px;
    background: var(--card);
    position: relative;
    overflow: hidden;
  }
  /* Front */
  .card-front {
    display: flex;
    flex-direction: column;
    align-items: center;
    text-align: center;
    padding-top: 150px;
  }
  .company-name {
    font-family: "Cinzel", serif;
    font-weight: 600;
    color: var(--blue);
    line-height: 1.15;
  }
  .company-name .primary { display: block; font-size: 40px; }
  .company-name .secondary { display: block; font-size: 15px; letter-spacing: 4px; margin-top: 6px; }
  .person { margin-top: 70px; font-family: "Cinzel", serif; }
  .person-name { font-size: 30px; font-weight: 400; }
  .person-name .first { color: var(--blue); }
  .person-name .last { color: var(--green); font-weight: 600; }
  .person-role { font-size: 17px; color: var(--green); letter-spacing: 0.5px; margin-top: 2px; }
  .icon-row {
    display: flex;
    align-items: center;
    gap: 6px;
    margin-top: 24px;
    width: 300px;
  }
  .icon-row .rule { flex: 1; height: 1px; background: var(--rule); }
  .icon-tile {
    width: 28px; height: 28px;
    background: var(--blue);
    border-radius: 4px;
    display: flex; align-items: center; justify-content: center;
  }
  .contact-list { margin-top: 16px; color: var(--ink); font-size: 17px; line-height: 1.5; }
  .contact-list .web-accent { color: var(--green); }
  .divider { width: 300px; height: 1px; background: var(--rule); margin: 14px 0; }
  .address { color: var(--ink); font-size: 17px; line-height: 1.45; }
  /* Back */
  .card-back { background: var(--card-deep); }
  .emboss-field {
    position: absolute;
    inset: 0;
    background: linear-gradient(160deg, var(--pattern-light) 0%, var(--pattern-dark) 55%, var(--card-deep) 100%);
  }
  .back-mark {
    position: absolute;
    left: 0; right: 0;
    bottom: 140px;
    display: flex;
    align-items: center;
    justify-content: center;
    gap: 8px;
    font-family: "Cinzel", serif;
    font-weight: 600;
    font-size: 16px;
    color: var(--green);
  }
  .back-mark .dot { width: 12px; height: 12px; border-radius: 50%; background: var(--blue); }
</style>
</head>
<body>
  <section class="card card-front">
    <h1 class="company-name">
      <span class="primary">Brambleford</span>
      <span class="secondary">LANDSCAPE CONSTRUCTION</span>
    </h1>
    <div class="person">
      <p class="person-name"><span class="first">CALLUM</span> <span class="last">REYES</span></p>
      <p class="person-role">MANAGING DIRECTOR</p>
    </div>
    <div class="icon-row">
      <span class="rule"></span>
      <span class="icon-tile">
        <svg width="16" height="16" viewBox="0 0 24 24" aria-label="Phone"><path fill="#fff" d="M6.6 10.8a15.1 15.1 0 0 0 6.6 6.6l2.2-2.2a1 1 0 0 1 1-.25 11.4 11.4 0 0 0 3.6.57 1 1 0 0 1 1 1V20a1 1 0 0 1-1 1A17 17 0 0 1 3 4a1 1 0 0 1 1-1h3.5a1 1 0 0 1 1 1c0 1.25.2 2.45.57 3.57a1 1 0 0 1-.25 1z"/></svg>
      </span>
      <span class="icon-tile">
        <svg width="16" height="16" viewBox="0 0 24 24" aria-label="Email"><rect x="3" y="5" width="18" height="14" rx="1" fill="none" stroke="#fff" stroke-width="2"/><path d="M3 6l9 7 9-7" fill="none" stroke="#fff" stroke-width="2"/></svg>
      </span>
      <span class="icon-tile">
        <svg width="16" height="16" viewBox="0 0 24 24" aria-label="Website"><circle cx="12" cy="12" r="9" fill="none" stroke="#fff" stroke-width="2"/><path d="M3 12h18M12 3c3 3 3 15 0 18M12 3c-3 3-3 15 0 18" fill="none" stroke="#fff" stroke-width="1.5"/></svg>
      </span>
      <span class="rule"></span>
    </div>
    <div class="contact-list">
      <p>061-308 775 214</p>
      <p>info@bramblefordyards.example</p>
      <p>www.<span class="web-accent">bramblefordyards</span>.example</p>
    </div>
    <span class="divider"></span>
    <div class="address">
      <p>18, Hollin Lane here</p>
      <p>78130, Eastmere</p>
    </div>
  </section>

  <section class="card card-back">
    <div class="emboss-field" role="img" aria-label="Tonal embossed repeat pattern of the company emblem covering the card back"></div>
    <div class="back-mark"><span class="dot"></span>Brambleford</div>
  </section>
</body>
</html>
```